Business Cards Design for the electrical wholesaler: clean bold dynamic :)

We need a business card design that would follow our latest brand guidelines. As an electrical wholesaler we want to bring a fresh look and feel into the industry. The design should be clean bold and dynamic. It should come alive with the renewed energy of our green colour. Our grey colour should keep things balanced and complement the notion of maturity and responsibility. We employ Lato as a corporate font however are not bound by this font and we’re open to interpretation here.

Target Market(s)

Electrical contractors

Industry/Entity Type

Business

Contact Information for Business Card

Logo
Name & Surname: Halyna Dorosh
Job Title: Director of Marketing
Email: halya.dorosh@quillmail.example
Cell phone: XXX.XXX.XXXX
Address: 20517 - 87 Ave. Edmonton, AB, Canada. T6K 4N8
Business Phone: 780.555.0184
Website: www.brovix.example

Font styles to use
Other font styles liked:
• Lato

Requirements
Must have
• Logo & website
Nice to have
• Brand elements - some of them you may find in the attached Brand Guidelines (e.g. three lines on the background signifying "W")

```html
<!DOCTYPE html>
<html lang="en">
<head>
<meta charset="utf-8">
<title>Brovix Business Cards</title>
<link href="https://fonts.googleapis.com/css2?family=Lato:wght@400;700;900&display=swap" rel="stylesheet">
<style>
  :root {
    --backdrop: #9b9b9b;
    --charcoal: #4a4b4d;
    --charcoal-deep: #3f4042;
    --charcoal-soft: #545557;
    --green: #7cb933;
    --paper: #ffffff;
    --paper-shade: #e9e9e9;
    --ink: #3d3e40;
  }
  * { box-sizing: border-box; margin: 0; padding: 0; }
  html, body {
    width: 1200px; height: 900px; overflow: hidden;
    background: var(--backdrop);
    font-family: "Lato", Arial, sans-serif;
  }
  .canvas { position: relative; width: 1200px; height: 900px; }
  .card {
    position: absolute; left: 250px; width: 700px; height: 400px;
    border-radius: 22px; overflow: hidden;
    box-shadow: 0 6px 18px rgba(0,0,0,0.28);
  }

  /* Back side */
  .card-back {
    top: 40px;
    background: linear-gradient(160deg, var(--charcoal-soft) 0%, var(--charcoal) 55%, var(--charcoal-deep) 100%);
  }
  .back-brand {
    position: absolute; left: 70px; bottom: 110px;
    display: flex; align-items: center; gap: 14px;
  }
  .brand-square { width: 26px; height: 26px; background: var(--green); }
  .back-brand .brand-name {
    font-weight: 700; font-size: 62px; color: var(--paper); letter-spacing: 1px; line-height: 1;
  }
  .back-tagline {
    position: absolute; left: 110px; bottom: 88px;
    font-size: 11px; letter-spacing: 2.5px; color: var(--paper); text-transform: uppercase;
  }
  .back-web {
    position: absolute; left: 110px; bottom: 44px;
    font-size: 17px; letter-spacing: 4px; color: var(--paper);
  }
  .back-web .accent { color: var(--green); }

  /* Front side */
  .card-front {
    top: 470px;
    background: linear-gradient(180deg, var(--paper) 0%, var(--paper) 45%, var(--paper-shade) 100%);
  }
  .front-band {
    position: absolute; left: 0; top: 0; bottom: 0; width: 100px;
    background: var(--charcoal);
  }
  .front-rule {
    position: absolute; left: 112px; top: 0; bottom: 0; width: 3px;
    background: var(--green);
  }
  .front-brand {
    position: absolute; left: 145px; top: 48px;
    display: flex; align-items: center; gap: 14px;
  }
  .front-brand .brand-name {
    font-weight: 700; font-size: 76px; color: var(--ink); line-height: 1; letter-spacing: 1px;
  }
  .person { position: absolute; left: 150px; top: 170px; }
  .person-name { font-weight: 900; font-size: 32px; color: var(--green); line-height: 1.05; }
  .person-title { font-size: 20px; color: var(--ink); margin-top: 2px; }
  .contacts { position: absolute; left: 150px; top: 262px; list-style: none; }
  .contacts li {
    display: flex; align-items: center; gap: 10px;
    font-size: 17px; color: var(--ink); height: 25px;
  }
  .contacts svg { width: 16px; height: 16px; flex: none; }
  .address {
    position: absolute; right: 44px; top: 230px; text-align: right;
    font-size: 17px; line-height: 1.45; color: var(--ink);
  }
</style>
</head>
<body>
<main class="canvas">

  <section class="card card-back" aria-label="Card back">
    <div class="back-brand">
      <span class="brand-square"></span>
      <span class="brand-name">brovix</span>
    </div>
    <p class="back-tagline">Electrical Wholesalers</p>
    <p class="back-web">www.<span class="accent">brovix</span>.example</p>
  </section>

  <section class="card card-front" aria-label="Card front">
    <div class="front-band"></div>
    <div class="front-rule"></div>

    <div class="front-brand">
      <span class="brand-square"></span>
      <span class="brand-name">brovix</span>
    </div>

    <div class="person">
      <h1 class="person-name">Halyna Dorosh</h1>
      <p class="person-title">Director of Marketing</p>
    </div>

    <ul class="contacts">
      <li>
        <svg viewBox="0 0 16 16" aria-hidden="true"><rect x="4" y="1" width="8" height="14" rx="1.5" fill="none" stroke="var(--green)" stroke-width="1.6"/><line x1="7" y1="12.5" x2="9" y2="12.5" stroke="var(--green)" stroke-width="1.4"/></svg>
        780.555.0184
      </li>
      <li>
        <svg viewBox="0 0 16 16" aria-hidden="true"><path d="M3 2 L6 2 L7 5.5 L5.3 6.8 C6.2 8.8 7.4 10 9.3 10.8 L10.5 9.1 L14 10 L14 13 C14 13.8 13.4 14 12.8 14 C7 13.6 2.4 9 2 3.2 C2 2.6 2.3 2 3 2 Z" fill="var(--green)"/></svg>
        780.555.0184
      </li>
      <li>
        <svg viewBox="0 0 16 16" aria-hidden="true"><rect x="1" y="3.5" width="14" height="9.5" fill="var(--green)"/><path d="M1 3.5 L8 9 L15 3.5" fill="none" stroke="var(--paper)" stroke-width="1.3"/></svg>
        halya.dorosh@quillmail.example
      </li>
      <li>
        <svg viewBox="0 0 16 16" aria-hidden="true"><g fill="none" stroke="var(--green)" stroke-width="1.3"><circle cx="8" cy="8" r="6.5"/><ellipse cx="8" cy="8" rx="2.8" ry="6.5"/><line x1="1.5" y1="8" x2="14.5" y2="8"/><line x1="2.6" y1="4.6" x2="13.4" y2="4.6"/><line x1="2.6" y1="11.4" x2="13.4" y2="11.4"/></g></svg>
        www.brovix.example
      </li>
    </ul>

    <address class="address" style="font-style: normal;">
      20517 - 87 Ave. Edmonton<br>
      AB, Canada. T6K 4N8
    </address>
  </section>

</main>
</body>
</html>
```